Leadership training for women Business + Spirit

I need a flyer for a leadership training to hand out after I've been doing public speaking. I would also like to send it as a PDF. so maybe A4 is a good size. I will probably also need a brochure, with some more in depth information, but to start with I like to just give them something so they get inspired to contact me for more information. You can see more of my style on www.brightmeadow.se . Its a training that combines business with spirit, heart with intellect. We focus both on strict leadership skills such as Setting objectives aligned with strategy, assess performance and spiritual practices such as meditation, connecting with your unique essence. I like the deign to communicate business and professional together with warmth, life and joy. Colourful with style. Empowerment. The attached style guide does not have to be followed strictly but please use it in combination with my site www.brightmeadow.se I've the logo in many different sizes. I've added the smallest one below. Use any images that you think might fit, doesn't have to be from my website, it could be from your resources. I've added some other images here in the brief too, I have many more but can't attach all of it :-).
Target Market(s)
Women in leadership positions age 30 - 60
Industry/Entity Type
Leadership
Look and feel

```html
<!DOCTYPE html>
<html lang="en">
<head>
<meta charset="utf-8">
<title>Bright Meadow – Leadership for Women</title>
<link href="https://fonts.googleapis.com/css2?family=Lato:wght@400;700;900&display=swap" rel="stylesheet">
<style>
  :root {
    --pink: #d8519a;
    --pink-deep: #c93a86;
    --orange: #f29a1f;
    --navy: #1b3350;
    --navy-deep: #142843;
    --white: #ffffff;
    --tan: #a89a7c;
  }
  * { box-sizing: border-box; margin: 0; padding: 0; }
  html, body { width: 950px; height: 1200px; overflow: hidden; }
  body { font-family: "Lato", sans-serif; background: var(--white); }
  .flyer { position: relative; width: 950px; height: 1200px; overflow: hidden; background: var(--white); }

  .header-art { position: absolute; left: 0; top: 0; width: 950px; height: 440px; }

  .intro { position: absolute; left: 315px; top: 54px; width: 572px; text-align: center; color: var(--white); }
  .intro-name { font-size: 29px; font-weight: 900; margin-bottom: 10px; }
  .intro-text { font-size: 14.3px; line-height: 18.7px; margin-bottom: 18px; }
  .intro-quote { font-size: 19px; font-weight: 700; margin-top: -12px; }

  .brand { position: absolute; left: 151px; top: 393px; display: flex; align-items: center; gap: 17px; }
  .brand-dot { width: 150px; height: 150px; border-radius: 50%; border: 3px solid var(--navy); flex: none; }
  .brand-name { font-size: 70px; font-weight: 400; color: var(--navy); letter-spacing: -1px; line-height: 1; }

  .mission { position: absolute; left: 31px; top: 561px; width: 887px; height: 108px; border: 4px solid var(--navy); padding: 22px 30px 0; text-align: center; }
  .mission-title { position: absolute; left: 50%; top: -22px; transform: translateX(-50%); background: var(--white); padding: 0 18px; font-size: 29px; font-weight: 900; color: var(--navy); white-space: nowrap; line-height: 1.2; }
  .mission-text { font-size: 14.3px; line-height: 18.8px; color: var(--navy); }

  .stories { position: absolute; left: 0; top: 695px; width: 950px; height: 452px;
    background: linear-gradient(180deg, #1f3a5c 0%, var(--navy) 45%, var(--navy-deep) 100%); }
  .story { position: absolute; top: 30px; width: 257px; text-align: center; }
  .story-photo { width: 257px; height: 162px; border: 4px solid var(--white); box-shadow: 3px 4px 8px rgba(0,0,0,.45); }
  .story-text { margin: 30px auto 0; width: 236px; font-size: 13.4px; line-height: 16.8px; color: var(--white); }
  .story--one { left: 45px; }
  .story--two { left: 345px; }
  .story--three { left: 646px; }
  .photo-shore { background: linear-gradient(180deg, #dfe3e6 0%, #c9c6c0 55%, #c4a98a 100%); }
  .photo-blossom { background: radial-gradient(circle at 55% 45%, #e79bc0 0%, #b5456f 40%, #3a2622 100%); }
  .photo-dunes { background: linear-gradient(160deg, #d9a672 0%, #c88b55 50%, #a96d3f 100%); }

  .contact { position: absolute; left: 0; top: 1147px; width: 950px; height: 53px; background: var(--tan);
    display: flex; align-items: center; justify-content: center; color: var(--white); font-size: 26px; font-weight: 900; }
</style>
</head>
<body>
<main class="flyer">

  <svg class="header-art" viewBox="0 0 950 440" xmlns="http://www.w3.org/2000/svg">
    <defs>
      <linearGradient id="pinkWash" x1="0" y1="0" x2="1" y2="1">
        <stop offset="0" stop-color="#e073ad"/>
        <stop offset="0.5" stop-color="#d8519a"/>
        <stop offset="1" stop-color="#c93a86"/>
      </linearGradient>
      <linearGradient id="portraitTone" x1="0" y1="0" x2="1" y2="1">
        <stop offset="0" stop-color="#6d5b50"/>
        <stop offset="0.55" stop-color="#8c7a6e"/>
        <stop offset="1" stop-color="#2c2d33"/>
      </linearGradient>
      <clipPath id="portraitClip">
        <circle cx="120" cy="180" r="186"/>
      </clipPath>
    </defs>
    <rect width="950" height="440" fill="url(#pinkWash)"/>
    <g clip-path="url(#portraitClip)">
      <rect x="0" y="0" width="320" height="440" fill="url(#portraitTone)" role="img" aria-label="Portrait photo of the coach in a white turtleneck and dark blazer"/>
    </g>
    <circle cx="120" cy="180" r="186" fill="none" stroke="var(--navy)" stroke-width="5" clip-path="inset(0 0 0 200px)"/>
    <path d="M0 392 C 240 350 560 400 950 342 L950 440 L0 440 Z" fill="var(--orange)"/>
    <path d="M0 418 C 240 368 570 420 950 358 L950 440 L0 440 Z" fill="var(--white)"/>
  </svg>

  <section class="intro">
    <h1 class="intro-name">Linnea Hallberg Ström</h1>
    <p class="intro-text">I am a modern mystic and leadership developer who has trained several hundreds of leaders on eg. Norrvik Bank, Ängsmjölk, Kornholm, Skobrant, Tryggvall, Vindora, Netlo. I have been on my spiritual journey since childhood, meditated since I was 16 and after a decade of extreme skiing and rock climbing I have weighted my adult professional life on the spiritual awakening and to coach people to a more living life.</p>
    <p class="intro-text">With BRIGHT MEADOW I offer opportunities for you as a woman to strengthen contact with your inner being and your own very holy wisdom. To unite the interior with the exterior and deepen your leadership, both as a private person and in your professional role. You are very welcome!</p>
    <p class="intro-quote">"I live as I learn, that's my strength."</p>
  </section>

  <div class="brand">
    <span class="brand-dot"></span>
    <span class="brand-name">Bright Meadow</span>
  </div>

  <section class="mission">
    <h2 class="mission-title">BRIGHT MEADOW</h2>
    <p class="mission-text">We have become good at performing at the expense of contact with our body and soul, when we really need the opposite. A holistic leadership of people who have good self-knowledge, who grow in the challenges, people who know that vulnerability gives an incomparable strength and does not underestimate their brilliant intellect. The world needs people who live and lead from a whole new place. The show feminine can lead us there.</p>
  </section>

  <section class="stories">
    <article class="story story--one">
      <div class="story-photo photo-shore" role="img" aria-label="Photo of a thoughtful woman standing on a beach"></div>
      <p class="story-text">As modern women, many of us share a basic pattern of just pushing through and biting, delivering and being good by driving over both body and soul. What if there is another way to get results? A way in which you combine practical skills in leadership such as goals, performance management and coaching with presence in both body, heart and soul. A way that lets soul, heart, achievement and business go hand in hand.</p>
    </article>
    <article class="story story--two">
      <div class="story-photo photo-blossom" role="img" aria-label="Photo of pink cherry blossoms on a branch"></div>
      <p class="story-text">Before spirituality became its own concept and concept, before the word even emerged or religions and new age seized it, it already existed as a natural part of our lives. We are all valuable just by being, without performing. We are all in contact with something bigger, everything is connected and is part of the same being. Life is sacred. Remembering and living this is spirituality for me.</p>
    </article>
    <article class="story story--three">
      <div class="story-photo photo-dunes" role="img" aria-label="Photo of a woman with arms raised joyfully in sand dunes"></div>
      <p class="story-text">We live in a culture that teaches us to shut down, keep the cover on our dreams and constantly put what is most important to us at the bottom of the list, while we are rushing towards a future that promises us all that we do not take time till now. Bright Meadow is a context that strengthens you, both as being and woman to wake up, grow and succeed with what you want to live before you die. It's empowerment!</p>
    </article>
  </section>

  <footer class="contact">0701-55 28 14 | BRIGHTMEADOW.SE | Folj oss pa: meadowbook</footer>

</main>
</body>
</html>
```